Business Card Design

Looking for business card designs for a new business. there will be two cards of the same design (both lots of information below in contact info). We would like the logo diagonally across the card with the information split above and below the logo similar to sketch. happy to look at similar alternatives
Please use same colours as in logo design

Industry/Entity Type

Business

Contact Information for Business Card

Dwight Halloran
mob - 0491 738 204
ph - 02 6148 3920
fax - 02 6148 3975
email - dwight@kestrelbeams.com.au
14 Larkmoor Road, Corrwell NSW 2371

Colin Marchetti
mob - 0438 912 557
ph - 02 6148 3920
fax - 02 6148 3975
email - colin@kestrelbeams.com.au

```html
<!DOCTYPE html>
<html lang="en">
<head>
<meta charset="utf-8">
<title>Kestrel Beams — Business Card</title>
<link rel="stylesheet" href="https://fonts.googleapis.com/css2?family=Open+Sans:wght@400;600;700&display=swap">
<style>
  :root {
    --teal: #127f79;
    --teal-text: #2b7e79;
    --ink: #111111;
    --body-text: #2a2a2a;
    --paper: #ffffff;
    --backdrop: #ececea;
  }
  * { box-sizing: border-box; margin: 0; padding: 0; }
  html, body {
    width: 1145px;
    height: 1200px;
    overflow: hidden;
    background: var(--backdrop);
    font-family: "Open Sans", Arial, sans-serif;
  }
  .canvas { position: relative; width: 1145px; height: 1200px; }

  .card {
    position: absolute;
    width: 942px;
    height: 541px;
    overflow: hidden;
  }
  .card--front { left: 167px; top: 22px; background: var(--paper); border: 1px solid #cfcfcf; }
  .card--back  { left: 29px;  top: 616px; background: var(--teal); }

  .brand {
    position: absolute;
    left: 0; right: 0;
    display: flex;
    justify-content: center;
    align-items: center;
    gap: 18px;
    color: var(--ink);
    font-weight: 700;
    font-size: 68px;
    letter-spacing: -1px;
    line-height: 1;
  }
  .brand__square { width: 56px; height: 56px; background: var(--ink); }
  .card--front .brand { top: 90px; }
  .card--back  .brand { top: 225px; font-size: 78px; }
  .card--back  .brand__square { width: 64px; height: 64px; }

  .holder {
    position: absolute;
    top: 254px; left: 0; right: 0;
    text-align: center;
    color: var(--teal-text);
    font-weight: 700;
    font-size: 29px;
  }
  .contact-line {
    position: absolute;
    left: 0; right: 0;
    display: flex;
    justify-content: center;
    align-items: center;
    gap: 6px;
    color: var(--body-text);
    font-size: 23px;
  }
  .contact-line--numbers { top: 336px; }
  .contact-line--email   { top: 379px; }
  .contact-line--address { top: 436px; }
  .contact-item { display: inline-flex; align-items: center; gap: 5px; }
  .icon { width: 20px; height: 20px; fill: var(--teal); flex: none; }

  .stripe { position: absolute; bottom: 0; height: 26px; }
  .stripe--left   { left: 0;     width: 307px; background: var(--teal); }
  .stripe--centre { left: 318px; width: 307px; background: var(--ink); }
  .stripe--right  { left: 637px; width: 305px; background: var(--teal); }

  .website {
    position: absolute;
    top: 428px; left: 0; right: 0;
    text-align: center;
    color: var(--paper);
    font-size: 28px;
    letter-spacing: 3px;
  }
  .website__domain { font-weight: 600; }
</style>
</head>
<body>
<div class="canvas">

  <section class="card card--front" aria-label="Business card front">
    <div class="brand"><span class="brand__square"></span><span class="brand__name">Kestrel Beams</span></div>

    <h1 class="holder">Colin Marchetti</h1>

    <div class="contact-line contact-line--numbers">
      <span class="contact-item">
        <svg class="icon" viewBox="0 0 24 24" aria-label="Phone"><path d="M6.6 10.8a15.1 15.1 0 0 0 6.6 6.6l2.2-2.2a1 1 0 0 1 1-.25 11.4 11.4 0 0 0 3.6.57 1 1 0 0 1 1 1V20a1 1 0 0 1-1 1A17 17 0 0 1 3 4a1 1 0 0 1 1-1h3.5a1 1 0 0 1 1 1c0 1.25.2 2.45.57 3.57a1 1 0 0 1-.25 1z"/></svg>
        02 6148 3920
      </span>
      <span class="contact-item">
        <svg class="icon" viewBox="0 0 24 24" aria-label="Mobile"><path d="M7 1h10a2 2 0 0 1 2 2v18a2 2 0 0 1-2 2H7a2 2 0 0 1-2-2V3a2 2 0 0 1 2-2zm0 3v13h10V4zm5 15a1.2 1.2 0 1 0 0 2.4A1.2 1.2 0 0 0 12 19z"/></svg>
        0438 912 557
      </span>
      <span class="contact-item">
        <svg class="icon" viewBox="0 0 24 24" aria-label="Fax"><path d="M7 3h10v5H7zM4 9h16a2 2 0 0 1 2 2v6h-4v4H6v-4H2v-6a2 2 0 0 1 2-2zm4 6v4h8v-4z"/></svg>
        02 6148 3975
      </span>
    </div>

    <div class="contact-line contact-line--email">
      <svg class="icon" viewBox="0 0 24 24" aria-label="Email"><path d="M2 9l10-6 10 6v11a1 1 0 0 1-1 1H3a1 1 0 0 1-1-1zm2 1.2V19h16v-8.8l-8 5z"/></svg>
      colin@kestrelbeams.com.au
    </div>

    <div class="contact-line contact-line--address">14 Larkmoor Road, Corrwell NSW 2371</div>

    <div class="stripe stripe--left"></div>
    <div class="stripe stripe--centre"></div>
    <div class="stripe stripe--right"></div>
  </section>

  <section class="card card--back" aria-label="Business card back">
    <div class="brand"><span class="brand__square"></span><span class="brand__name">Kestrel Beams</span></div>
    <p class="website">www.<span class="website__domain">kestrelbeams</span>.com.au</p>
  </section>

</div>
</body>
</html>
```